Road Construction Company needs business cards

We would like a new business card designed for our business.

We're a road construction company based in Qld, Australia.

Can the business card please have the following information on it.

Name: Warren Halbeck
Position: General Manager
Phone: 0472 915 348
Email: Warren.halbeck@tovrin.com.au
Address: 87 Marrow Ave, Pendlebay, QLD, 4023
Website: www.tovrin.com.au

Visually we'd like the card to be professional and simple.

Attached is our logo.

Our website is www.tovrin.com.au

Target Market(s)

Men aged 25-60

Contact Information for Business Card

As listed in project description

Font styles to use
Serif

Requirements
Must have
• Large logo on back of card

```html
<!DOCTYPE html>
<html lang="en">
<head>
<meta charset="utf-8">
<title>Tovrin Road Construction – Business Card</title>
<link href="https://fonts.googleapis.com/css2?family=Poppins:wght@400;600;800&display=swap" rel="stylesheet">
<style>
  :root {
    --backdrop: #202020;
    --backdrop-edge: #0c0c0c;
    --card-dark: #171717;
    --card-light: #ffffff;
    --navy: #0b4ea2;
    --sky: #35a7da;
    --text-light: #ffffff;
    --emboss: #333333;
  }
  * { box-sizing: border-box; margin: 0; padding: 0; }
  html, body { width: 1200px; height: 1015px; overflow: hidden; }
  body {
    background: radial-gradient(ellipse at center, var(--backdrop) 0%, var(--backdrop-edge) 100%);
    font-family: "Poppins", sans-serif;
    position: relative;
  }
  .card {
    position: absolute;
    left: 300px;
    width: 600px;
    height: 343px;
    overflow: hidden;
    box-shadow: 0 18px 40px rgba(0,0,0,.6);
  }
  .card--back { top: 120px; background: var(--card-dark); }
  .card--front { top: 552px; background: var(--card-light); }

  .wordmark {
    position: absolute;
    font-weight: 800;
    letter-spacing: 2px;
    line-height: 1;
  }
  .card--back .wordmark {
    left: 0; right: 0; top: 132px;
    text-align: center;
    font-size: 72px;
    color: var(--emboss);
  }
  .card--front .wordmark {
    left: 48px; top: 112px;
    font-size: 56px;
    color: var(--navy);
  }

  .wave { position: absolute; inset: 0; }

  .person {
    position: absolute;
    right: 40px; top: 22px;
    text-align: right;
  }
  .person__name {
    font-weight: 800;
    font-size: 19px;
    color: var(--navy);
    letter-spacing: .3px;
  }
  .person__role {
    font-size: 15px;
    color: var(--sky);
    margin-top: -2px;
  }

  .contact {
    position: absolute;
    right: 30px; top: 160px;
    list-style: none;
    color: var(--text-light);
    font-size: 13.5px;
    line-height: 1.35;
    text-align: right;
  }
  .contact__item {
    display: flex;
    justify-content: flex-end;
    align-items: flex-start;
    gap: 8px;
    margin-bottom: 3px;
  }
  .contact__icon { width: 14px; height: 14px; flex: none; margin-top: 3px; }
</style>
</head>
<body>

  <section class="card card--back" aria-label="Card back">
    <div class="wordmark">TOVRIN</div>
  </section>

  <section class="card card--front" aria-label="Card front">
    <svg class="wave" viewBox="0 0 600 343" aria-hidden="true">
      <path d="M70,343 C230,350 270,250 330,175 C390,100 460,100 600,100" fill="none" stroke="var(--sky)" stroke-width="7" transform="translate(-20,-22)"/>
      <path d="M70,343 C230,350 270,250 330,175 C390,100 460,100 600,100" fill="none" stroke="var(--navy)" stroke-width="7" transform="translate(-8,-10)"/>
      <path d="M70,343 C230,350 270,250 330,175 C390,100 460,100 600,100 L600,343 Z" fill="var(--card-dark)"/>
    </svg>

    <div class="wordmark">TOVRIN</div>

    <div class="person">
      <div class="person__name">WARREN HALBECK</div>
      <div class="person__role">General Manager</div>
    </div>

    <ul class="contact">
      <li class="contact__item">
        <span>87 Marrow Ave<br>Pendlebay, QLD, 4023</span>
        <svg class="contact__icon" viewBox="0 0 14 14" aria-hidden="true"><path d="M7 1a4.2 4.2 0 0 0-4.2 4.2C2.8 8.5 7 13 7 13s4.2-4.5 4.2-7.8A4.2 4.2 0 0 0 7 1zm0 5.8a1.6 1.6 0 1 1 0-3.2 1.6 1.6 0 0 1 0 3.2z" fill="var(--navy)"/></svg>
      </li>
      <li class="contact__item">
        <span>0472 915 348</span>
        <svg class="contact__icon" viewBox="0 0 14 14" aria-hidden="true"><path d="M3 1.5l2.2 2.6-1.2 1.5a8 8 0 0 0 4.4 4.4l1.5-1.2 2.6 2.2-1.3 1.5C6 12 2 8 1.5 2.8z" fill="var(--navy)"/></svg>
      </li>
      <li class="contact__item">
        <span>Warren.halbeck@tovrin.com.au</span>
        <svg class="contact__icon" viewBox="0 0 14 14" aria-hidden="true"><rect x="1" y="3" width="12" height="8.5" fill="var(--navy)"/><path d="M1 3l6 5 6-5" fill="none" stroke="var(--text-light)" stroke-width="1"/></svg>
      </li>
      <li class="contact__item">
        <span>www.tovrin.com.au</span>
        <svg class="contact__icon" viewBox="0 0 14 14" aria-hidden="true"><circle cx="7" cy="7" r="5.8" fill="var(--navy)"/><path d="M1.2 7h11.6M7 1.2v11.6M7 1.2c-3 3-3 8.6 0 11.6M7 1.2c3 3 3 8.6 0 11.6" fill="none" stroke="var(--text-light)" stroke-width=".8"/></svg>
      </li>
    </ul>
  </section>

</body>
</html>
```